LANTERN - and the quiet crafts of everyday life

I´m writing a book about CHANGE and the skills leaders needs to embody the transformation from being amanager to become leaders.
The title of the book in Icelandic is the same as the name of the project (which I want to be used on the designes is:) UPPSPRETTA
(with the subtitle:) og hugrekki hversdagsins

Change is not controlled or managed – Leading effective change is an art form which is one of the big reasons for why 70% of changes within companies fail. The main reason however, is that managers are tasked with managing and directing them. The art form of change is to put it in the hands of leaders who possess the emotional intelligence that is needed – all their other advantages intact – to lead change all the way.

The big problem when it comes to change is that there are too many managers and too few leaders within companies – leaders who possess emotional intelligence which is the most important skill a leader embodies to empower change. A leader has what it takes to empower followership.

A manager tends to push and control, make decisions that he presupposes others to implement the way he expects. An emotionally competent leader leads by example and enhances followership on that journey because of the trust and respect he has earned.

In few words: SOFT SKILLS ARE THE NEW HARD SKILLS!

```html
<!DOCTYPE html>
<html lang="is">
<head>
<meta charset="utf-8">
<title>Uppspretta – og hugrekki hversdagsins</title>
<link rel="stylesheet" href="https://fonts.googleapis.com/css2?family=Roboto:wght@700&family=Fira+Sans:wght@300&display=swap">
<style>
  :root {
    --page-bg: #ffffff;
    --cover-top: #d9614a;
    --cover-mid: #c9402f;
    --cover-bottom: #a92020;
    --cover-edge: #e9735a;
    --title-ink: #f4eeee;
    --subtitle-ink: #f6e6e2;
    --rule: rgba(240, 170, 150, 0.75);
    --art-glow: #f2c6d0;
    --art-rose: #c45a78;
    --art-plum: #6e1d3a;
  }
  html, body {
    margin: 0;
    padding: 0;
    width: 1200px;
    height: 800px;
    overflow: hidden;
    background: var(--page-bg);
  }
  .canvas {
    position: relative;
    width: 1200px;
    height: 800px;
  }
  .book-cover {
    position: absolute;
    left: 360px;
    top: 40px;
    width: 480px;
    height: 720px;
    background:
      linear-gradient(100deg, rgba(255,180,150,0.25) 0%, rgba(255,180,150,0) 45%, rgba(255,160,130,0.2) 100%),
      linear-gradient(180deg, var(--cover-top) 0%, var(--cover-mid) 45%, var(--cover-bottom) 100%);
    overflow: hidden;
  }
  .cover-title {
    position: absolute;
    top: 92px;
    left: 0;
    width: 100%;
    margin: 0;
    text-align: center;
    font-family: "Roboto", "Helvetica Neue", Arial, sans-serif;
    font-weight: 700;
    font-size: 62px;
    letter-spacing: 0.5px;
    line-height: 1;
    color: var(--title-ink);
  }
  .cover-art {
    position: absolute;
    left: 20px;
    top: 200px;
    width: 440px;
    height: 440px;
  }
  .cover-subtitle {
    position: absolute;
    left: 93px;
    top: 614px;
    width: 293px;
    height: 45px;
  }
  .cover-subtitle::before,
  .cover-subtitle::after {
    content: "";
    position: absolute;
    left: 0;
    width: 100%;
    height: 1px;
    background: linear-gradient(90deg, rgba(240,170,150,0) 0%, var(--rule) 15%, var(--rule) 85%, rgba(240,170,150,0) 100%);
  }
  .cover-subtitle::before { top: 0; }
  .cover-subtitle::after { bottom: 0; }
  .cover-subtitle p {
    margin: 0;
    line-height: 45px;
    text-align: center;
    font-family: "Fira Sans", "Helvetica Neue", Arial, sans-serif;
    font-weight: 300;
    font-size: 23px;
    letter-spacing: 0.3px;
    color: var(--subtitle-ink);
  }
</style>
</head>
<body>
  <main class="canvas">
    <section class="book-cover">
      <h1 class="cover-title">UPPSPRETTA</h1>

      <svg class="cover-art" viewBox="0 0 440 440" role="img"
           aria-label="Illustration of a glowing globe with orbiting network lines above silhouettes of business people meeting around a table">
        <defs>
          <radialGradient id="art-globe" cx="0.58" cy="0.42" r="0.55">
            <stop offset="0" stop-color="var(--art-glow)" stop-opacity="0.95"/>
            <stop offset="0.5" stop-color="var(--art-rose)" stop-opacity="0.75"/>
            <stop offset="1" stop-color="var(--art-plum)" stop-opacity="0"/>
          </radialGradient>
          <linearGradient id="art-ground" x1="0" y1="0" x2="0" y2="1">
            <stop offset="0" stop-color="var(--art-plum)" stop-opacity="0.7"/>
            <stop offset="1" stop-color="var(--art-plum)" stop-opacity="0"/>
          </linearGradient>
        </defs>
        <ellipse cx="220" cy="190" rx="210" ry="190" fill="url(#art-globe)"/>
        <ellipse cx="230" cy="370" rx="210" ry="60" fill="url(#art-ground)"/>
      </svg>

      <div class="cover-subtitle">
        <p>og hugrekki hversdagsins</p>
      </div>
    </section>
  </main>
</body>
</html>
```